Photography business - business card design quick turn around

Create a business card design for me please. I actually need the final design back before the end of Sunday 13th May 7pm GMT. Sorry for the short notice.

Photoshop artwork template uploaded with artwork guidelines including printer profiles and other mandatory specifications. Only one side of the business card is required as the other side will be an image.

The design is required as an unflattened PSD file so that I can edit the text if I need to.

My brand colours are white and the teal you see in the logo. Occasionally I also use a dark grey on my website (I don't mind the shade of grey as appreciate grey on teal would be a different grey, to the grey I use on white on the website, so just use a shade of grey that matches). Font can be as the font for the logo or if you prefer I am open to another sans serif, easily legible font. Ideally font size will be 12+.Please do not use capital letters for text. I prefer everything to be lower case, if possible.

Thank you.

Lena

Target Market(s)

Other business owners who may refer me and families

Industry/Entity Type

Photographer

Contact Information for Business Card

Silver Kettle Photography Logo
Sub text: family portraiture, captured with love

Contact information, ideally using simple icons to represent email / website / facebook / instagram / pinterest

email: lena@silverkettlephotography.co.uk
website: silverkettlephotography.co.uk
facebook: @silverkettlephotography
pinterest: pinterest.com/silverkettlepho
instagram: @silverkettle_photography
mobile/telephone: 07713460291

If there is too much text then please drop the instagram and pinterest information.

Font styles to use
Sans Serif

Colors
33b8a4

Requirements
Must have
• Logo
• Contact details as listed above
• sub text
Nice to have
• Instagram and Pinterest contact details
• Nice to have icons to represent website / phone / facebook etc followered by the handle where relevant

```html
<!DOCTYPE html>
<html lang="en">
<head>
<meta charset="utf-8">
<title>Silver Kettle Photography – business card</title>
<link href="https://fonts.googleapis.com/css2?family=Questrial&display=swap" rel="stylesheet">
<style>
  :root {
    --teal: #22cfbc;
    --ink: #1f1f1f;
    --card: #ffffff;
    --backdrop: #4b4b4d;
  }
  * { margin: 0; padding: 0; box-sizing: border-box; }
  html, body {
    width: 1200px;
    height: 1000px;
    overflow: hidden;
    background: var(--backdrop);
    font-family: "Questrial", sans-serif;
  }
  .card {
    position: absolute;
    left: 150px;
    top: 243px;
    width: 900px;
    height: 514px;
    background: var(--card);
    border-radius: 34px;
    overflow: hidden;
    color: var(--ink);
  }
  .card__band {
    position: absolute;
    left: 0; right: 0; bottom: 0;
    height: 22px;
    background: var(--teal);
  }
  .brand {
    position: absolute;
    left: 60px;
    top: 70px;
    width: 380px;
  }
  .brand__name {
    display: flex;
    align-items: center;
    gap: 14px;
    color: var(--teal);
    font-size: 36px;
    line-height: 1.1;
    letter-spacing: 0.5px;
    font-weight: 400;
  }
  .brand__dot {
    flex: none;
    width: 22px;
    height: 22px;
    border-radius: 50%;
    background: var(--teal);
  }
  .brand__rule {
    margin-top: 16px;
    height: 2px;
    background: var(--ink);
  }
  .brand__tagline {
    margin-top: 6px;
    font-size: 20px;
    letter-spacing: 0.3px;
  }
  .contact {
    position: absolute;
    list-style: none;
    font-size: 21px;
  }
  .contact li {
    display: flex;
    align-items: center;
    gap: 10px;
    height: 30px;
  }
  .contact--direct { left: 60px; top: 300px; }
  .contact--social { left: 470px; top: 372px; }
  .icon {
    flex: none;
    width: 18px;
    height: 18px;
  }
  .icon circle { fill: var(--teal); }
  .icon path { fill: none; stroke: #fff; stroke-width: 1.6; stroke-linecap: round; stroke-linejoin: round; }
</style>
</head>
<body>
  <main class="card">
    <header class="brand">
      <h1 class="brand__name"><span class="brand__dot"></span>silver kettle photography</h1>
      <div class="brand__rule"></div>
      <p class="brand__tagline">family portraiture, captured with love</p>
    </header>

    <ul class="contact contact--direct">
      <li>
        <svg class="icon" viewBox="0 0 18 18"><circle cx="9" cy="9" r="9"/><path d="M6 5l1.6 0 .8 2-1 1c.6 1.2 1.4 2 2.6 2.6l1-1 2 .8v1.6c-4 .4-7.4-3-7-7z"/></svg>
        07713460291
      </li>
      <li>
        <svg class="icon" viewBox="0 0 18 18"><circle cx="9" cy="9" r="9"/><path d="M4.5 6h9v6h-9z M4.5 6l4.5 3.5 4.5-3.5"/></svg>
        lena@silverkettlephotography.co.uk
      </li>
      <li>
        <svg class="icon" viewBox="0 0 18 18"><circle cx="9" cy="9" r="9"/><path d="M9 4a5 5 0 1 0 .01 0z M4 9h10 M9 4c-2 2.7-2 7.3 0 10 M9 4c2 2.7 2 7.3 0 10"/></svg>
        silverkettlephotography.co.uk
      </li>
    </ul>

    <ul class="contact contact--social">
      <li>
        <svg class="icon" viewBox="0 0 18 18"><circle cx="9" cy="9" r="9"/></svg>
        @silverkettlephotography
      </li>
      <li>
        <svg class="icon" viewBox="0 0 18 18"><circle cx="9" cy="9" r="9"/></svg>
        silverkettlepho
      </li>
      <li>
        <svg class="icon" viewBox="0 0 18 18"><circle cx="9" cy="9" r="9"/></svg>
        @silverkettle_photography
      </li>
    </ul>

    <div class="card__band"></div>
  </main>
</body>
</html>
```